Buch-/eBook-Cover für Traumatherapeutin
Zielgruppe
Ich bin Traumatherapeutin und schreibe ein Buch zum Thema Trauma bearbeiten.
Meine Zielgruppe sucht Heilung, Genesung, Selbstliebe etc.
Aufgabenstellung
Buchcover
Bitte erstell mir ein modernes positives inspirierendes Buchcover mit dem
Titel: 'Morgenlicht NEU entdecken“
Untertitel: „Spüre den Mut der ganz in dir wohnt“
Dr. Mira Kessow
Ich hätte gerne ein modernes Buch, das entweder einen Bezug zum Thema Trauma hat oder aber einfach stylische Schriftzüge. Bin aber auch offen für andere Vorschläge.
Dunkelblau, weiß und türkis oder auch rosa mag ich ganz gerne. Wobei Dunkelblau, weiß und türkis meine Favoriten sind und mit rosa höchstens kleinere Akzente gesetzt werden sollten.
Das Buchcover soll modern sein und direkt ansprechen. Gerne eine originelle Lösung, oder etwas Besonderes, etwas das Tiefe ausdrückt, oder man mehrmals hinsehen muss um etwas zu erkennen oder etwas das mehr Interpretationsspielraum lässt.
Gerne auch viel weiß, zumindest heller und nicht zu dunkel. Stylish, aber nicht überfrachtet.
Schreib mich gerne an, wenn du Fragen hast.
Ich habe mal zwei Beispiel von Typolösungen angehängt, die ich ganz cool fände.
Ich freue mich auf deine Ideen :-)
Ganz liebe Grüße
Mira

```html
<!DOCTYPE html>
<html lang="de">
<head>
<meta charset="utf-8">
<title>Morgenlicht NEU entdecken – Dr. Mira Kessow</title>
<link href="https://fonts.googleapis.com/css2?family=Bebas+Neue&family=Open+Sans:ital,wght@0,400;1,400&family=Sacramento&display=swap" rel="stylesheet">
<style>
  :root {
    --bg-top: #d7a8c5;
    --bg-mid: #bcc0c8;
    --bg-bottom: #a5d6cf;
    --violet: #5a3a8f;
    --white: #ffffff;
    --rose-line: #e58cc1;
    --rose-soft: #ec9a9f;
    --teal-line: #7dbcb2;
  }
  html, body {
    margin: 0;
    padding: 0;
    overflow: hidden;
    background: #ffffff;
  }
  .cover {
    position: relative;
    width: 858px;
    height: 1200px;
    overflow: hidden;
    background: linear-gradient(170deg, var(--bg-top) 0%, var(--bg-mid) 30%, var(--bg-bottom) 62%, var(--bg-bottom) 100%);
  }
  .decor {
    position: absolute;
    inset: 0;
  }
  .author {
    position: absolute;
    top: 20px;
    left: 0;
    width: 100%;
    text-align: center;
    font-family: "Open Sans", sans-serif;
    font-size: 24px;
    color: var(--white);
    margin: 0;
  }
  .title {
    margin: 0;
    font-weight: normal;
  }
  .title-script {
    position: absolute;
    font-family: "Sacramento", cursive;
    color: var(--violet);
    line-height: 1;
    white-space: nowrap;
  }
  .title-script--top {
    left: 58px;
    top: 300px;
    font-size: 150px;
  }
  .title-script--bottom {
    right: 58px;
    top: 625px;
    font-size: 138px;
    z-index: 3;
  }
  .title-block {
    position: absolute;
    left: 0;
    top: 462px;
    width: 858px;
    text-align: center;
    font-family: "Bebas Neue", sans-serif;
    font-size: 228px;
    line-height: 1;
    z-index: 2;
  }
  .title-block span {
    position: relative;
    display: inline-block;
    color: var(--white);
  }
  .title-block span::before {
    content: attr(data-text);
    position: absolute;
    left: 12px;
    top: -9px;
    color: var(--violet);
    z-index: -1;
  }
  .subtitle {
    position: absolute;
    right: 52px;
    top: 762px;
    margin: 0;
    text-align: right;
    font-family: "Open Sans", sans-serif;
    font-style: italic;
    font-size: 27px;
    line-height: 1.35;
    color: var(--violet);
  }
  .head-art {
    position: absolute;
    left: 0;
    top: 540px;
    width: 440px;
    height: 660px;
  }
</style>
</head>
<body>
<main class="cover">
  <svg class="decor" width="858" height="1200" viewBox="0 0 858 1200">
    <defs>
      <linearGradient id="roseBand" x1="0" y1="0" x2="1" y2="1">
        <stop offset="0" stop-color="#e58cc1" stop-opacity="0.35"/>
        <stop offset="1" stop-color="#e58cc1" stop-opacity="0.15"/>
      </linearGradient>
      <linearGradient id="tealBand" x1="0" y1="0" x2="1" y2="1">
        <stop offset="0" stop-color="#7dbcb2" stop-opacity="0.3"/>
        <stop offset="1" stop-color="#7dbcb2" stop-opacity="0.5"/>
      </linearGradient>
    </defs>
    <g role="img" aria-label="Feines rosa Linienmuster in diagonalen Feldern oben rechts">
      <polygon points="320,0 858,0 858,440 560,230" fill="url(#roseBand)"/>
      <line x1="320" y1="0" x2="858" y2="440" stroke="var(--rose-line)" stroke-width="2.5"/>
      <line x1="390" y1="0" x2="858" y2="385" stroke="var(--rose-line)" stroke-width="2.5"/>
      <line x1="440" y1="0" x2="858" y2="345" stroke="var(--rose-line)" stroke-width="2.5"/>
    </g>
    <g role="img" aria-label="Feines türkises Linienmuster in diagonalen Feldern unten">
      <polygon points="0,740 300,900 858,1200 0,1200" fill="url(#tealBand)"/>
      <polygon points="470,1200 858,980 858,1200" fill="url(#tealBand)"/>
      <line x1="0" y1="740" x2="858" y2="1200" stroke="var(--teal-line)" stroke-width="3"/>
      <line x1="0" y1="790" x2="760" y2="1200" stroke="var(--teal-line)" stroke-width="3"/>
      <line x1="470" y1="1200" x2="858" y2="980" stroke="var(--teal-line)" stroke-width="3"/>
    </g>
  </svg>

  <svg class="head-art" width="440" height="660" viewBox="0 0 440 660" role="img" aria-label="Linienzeichnung eines Kopfes im Profil mit verschlungenen Gedankenlinien">
    <defs>
      <radialGradient id="headTone" cx="0.45" cy="0.35" r="0.6">
        <stop offset="0" stop-color="#ec9a9f" stop-opacity="0.35"/>
        <stop offset="1" stop-color="#ec9a9f" stop-opacity="0"/>
      </radialGradient>
    </defs>
    <rect width="440" height="660" fill="url(#headTone)"/>
  </svg>

  <p class="author">Dr. Mira Kessow</p>

  <h1 class="title">
    <span class="title-script title-script--top">Morgenlicht</span>
    <span class="title-block"><span data-text="NEU">NEU</span></span>
    <span class="title-script title-script--bottom">entdecken</span>
  </h1>

  <p class="subtitle">Spüre den Mut<br>der ganz in dir wohnt</p>
</main>
</body>
</html>
```